Dietitian needs awesome business card

I need a contemporary design that's eye catching but professional.
My card is to given to doctors, specialists and patients alike.
I manage patients with chronic diseases
I have uploaded my logo and current business card, I would also like the other Certified Clinical Nutritionist logo incorporated into the design

Target Market(s)

Doctors, specialists and patients

Industry/Entity Type

Healthcare

Contact Information for Business Card

www.brightfieldnutrition.com.au
Ph: 0427 561 903
Fax: 6457 2183
email: marcus.k.diet@fernmail.com
Space on the back of the card with: Appointment date, Appointment time and appointment location

Font styles to use
Serif

Colors
fbee3e
876aae
ffc214

Requirements
Must have
• My Logo
• Certified Clinical Nutritionist Logo
• My 4 locations - Pinebrook Medical Centre, North Corrin Health, Hollis Medical, Ashcombe Doctors Surgery
Nice to have
• I like the colours in my current business card

```html
<!DOCTYPE html>
<html lang="en">
<head>
<meta charset="utf-8">
<title>Brightfield Nutrition – Business Card</title>
<link rel="stylesheet" href="https://fonts.googleapis.com/css2?family=Lora:wght@400;500&family=Montserrat:wght@400;500;600&display=swap">
<style>
  :root {
    --page: #e9eaee;
    --card: #ffffff;
    --navy: #283a8f;
    --navy-ink: #1f2f86;
    --leaf: #7cc242;
    --leaf-dark: #4cae3a;
    --badge: #f47b20;
    --white: #ffffff;
  }
  * { box-sizing: border-box; margin: 0; padding: 0; }
  html, body { width: 1200px; height: 900px; overflow: hidden; }
  body {
    background: var(--page);
    position: relative;
    font-family: "Montserrat", Arial, sans-serif;
  }
  .card {
    position: absolute;
    width: 680px;
    height: 390px;
    border-radius: 26px;
    background: var(--card);
    overflow: hidden;
    box-shadow: 0 8px 24px rgba(0,0,0,0.12);
  }
  .card--appointment { left: 150px; top: 45px; }
  .card--contact { left: 370px; top: 465px; }

  .brand {
    position: absolute;
    display: flex;
    align-items: center;
    gap: 12px;
  }
  .brand__dot {
    width: 44px; height: 44px;
    border-radius: 50%;
    background: var(--leaf);
    flex: none;
  }
  .brand__name {
    font-family: "Lora", Georgia, serif;
    font-weight: 500;
    font-size: 34px;
    color: var(--navy-ink);
    line-height: 1;
  }
  .card--appointment .brand { left: 48px; top: 118px; }

  .appointment {
    position: absolute;
    left: 110px;
    top: 190px;
    width: 520px;
    color: var(--navy-ink);
    font-size: 15px;
  }
  .appointment__title {
    color: var(--leaf-dark);
    font-weight: 600;
    font-size: 19px;
    margin-bottom: 14px;
  }
  .field-row { display: flex; align-items: flex-end; gap: 8px; margin-bottom: 22px; }
  .field__label { white-space: nowrap; }
  .field__line { flex: 1; border-bottom: 1.5px solid var(--navy-ink); height: 18px; }
  .credentials {
    font-family: "Lora", Georgia, serif;
    font-size: 17px;
    color: var(--navy-ink);
    margin-top: 6px;
  }

  .contact-panel {
    position: absolute;
    left: 262px; top: 0;
    width: 418px; height: 100%;
    background: var(--navy);
    border-left: 3px solid var(--leaf);
  }
  .contact-panel__notch {
    position: absolute;
    left: -14px; top: 128px;
    width: 0; height: 0;
    border-top: 12px solid transparent;
    border-bottom: 12px solid transparent;
    border-right: 12px solid var(--navy);
  }
  .card--contact .brand { left: 30px; top: 205px; gap: 10px; }
  .card--contact .brand__dot { width: 38px; height: 38px; }
  .card--contact .brand__name { font-size: 28px; line-height: 1.1; }

  .person {
    position: absolute;
    left: 34px; top: 120px;
    font-family: "Lora", Georgia, serif;
    font-size: 26px;
    color: var(--white);
  }
  .person__surname { color: var(--leaf); }
  .contact-list {
    position: absolute;
    left: 34px; top: 166px;
    list-style: none;
    color: var(--white);
    font-size: 15px;
  }
  .contact-list li { display: flex; align-items: center; gap: 10px; margin-bottom: 7px; }
  .contact-list svg { width: 13px; height: 13px; flex: none; }
  .cert-badge {
    position: absolute;
    right: 30px; bottom: 30px;
    width: 150px; height: 64px;
    background: var(--badge);
  }
</style>
</head>
<body>

<section class="card card--appointment" aria-label="Card back: appointment">
  <div class="brand">
    <span class="brand__dot"></span>
    <span class="brand__name">Brightfield Nutrition</span>
  </div>
  <div class="appointment">
    <p class="appointment__title">Appointment:</p>
    <div class="field-row">
      <span class="field__label">Date:</span><span class="field__line"></span>
      <span class="field__label">Time:</span><span class="field__line"></span>
    </div>
    <div class="field-row">
      <span class="field__label">Location:</span><span class="field__line"></span>
    </div>
    <p class="credentials">Certified Clinical Nutritionist, Nutritionist and Chef</p>
  </div>
</section>

<section class="card card--contact" aria-label="Card front: contact details">
  <div class="brand">
    <span class="brand__dot"></span>
    <span class="brand__name">Brightfield<br>Nutrition</span>
  </div>
  <div class="contact-panel">
    <span class="contact-panel__notch"></span>
    <p class="person">Marcus <span class="person__surname">Kellaway</span></p>
    <ul class="contact-list">
      <li>
        <svg viewBox="0 0 16 16" aria-hidden="true"><path fill="#7cc242" d="M3 1l3 3-2 2c1 2 3 4 5 5l2-2 3 3-2 3C7 15 1 9 1 3z"/></svg>
        0427 561 903
      </li>
      <li>
        <svg viewBox="0 0 16 16" aria-hidden="true"><rect x="2" y="5" width="12" height="9" rx="1" fill="#7cc242"/><rect x="4" y="1" width="8" height="5" fill="#7cc242"/></svg>
        6457 2183
      </li>
      <li>
        <svg viewBox="0 0 16 16" aria-hidden="true"><rect x="1.5" y="3.5" width="13" height="9" fill="none" stroke="#7cc242" stroke-width="1.5"/><path d="M2 4l6 5 6-5" fill="none" stroke="#7cc242" stroke-width="1.5"/></svg>
        marcus.k.diet@fernmail.com
      </li>
      <li>
        <svg viewBox="0 0 16 16" aria-hidden="true"><circle cx="8" cy="8" r="6.5" fill="none" stroke="#7cc242" stroke-width="1.5"/><path d="M1.5 8h13M8 1.5c-3 3.5-3 9.5 0 13M8 1.5c3 3.5 3 9.5 0 13" fill="none" stroke="#7cc242" stroke-width="1.2"/></svg>
        www.brightfieldnutrition.com.au
      </li>
    </ul>
    <div class="cert-badge" role="img" aria-label="Certification badge"></div>
  </div>
</section>

</body>
</html>
```